Private Investment Firm Needs PowerPoint Presentation Template

Design PowerPoint template, take Pinebrook-submitted rough presentation draft, and drop it into new template. See attached Project Brief file for more detail.
Updates

Some decent designs have been submitted but they seem to lack the understanding of our target markets. I am hopeful that more time and feedback will result in better results.

Target Market(s)

Private company owners and intermediaries.

Font styles to use
Serif

Colors
3176b5

Requirements
Must have
• See attached Project Brief.
Nice to have
Should not have
• No B2C fluff--this is a B2B project.

```html
<!DOCTYPE html>
<html lang="en">
<head>
<meta charset="utf-8">
<title>Pinebrook Capital – Deck Slides</title>
<link href="https://fonts.googleapis.com/css2?family=Raleway:wght@500;600;700;800&display=swap" rel="stylesheet">
<style>
:root{
  --navy:#264a6b;
  --blue:#1a72b8;
  --accent:#3176b5;
  --ink:#3b3b3b;
  --dark:#1f2f40;
  --empty:#e8e8e8;
  --gap:#ffffff;
}
*{box-sizing:border-box;margin:0;padding:0}
html,body{width:1200px;height:1200px;overflow:hidden;background:var(--gap)}
body{font-family:"Raleway",Arial,sans-serif;position:relative}
.slide{position:absolute;width:397px;height:396px;background:#fff;overflow:hidden}
.empty{background:var(--empty)}
.top-bar{position:absolute;left:0;top:0;width:397px;height:22px}
.foot{position:absolute;left:0;top:370px;width:397px;height:26px}
.page-num{position:absolute;top:377px;left:170px;width:60px;text-align:center;color:#fff;font-weight:700;font-size:10px}
.brand{position:absolute;top:368px;left:306px;display:flex;align-items:center;gap:4px;font-weight:700;font-size:9.5px;color:var(--navy);letter-spacing:.5px}
.brand .dot{width:11px;height:11px;border-radius:50%;background:var(--accent)}
.title{position:absolute;left:0;top:44px;width:397px;text-align:center;color:var(--blue);font-weight:800;font-size:22.5px;line-height:22px}
.q{position:absolute;left:10px;right:10px;color:var(--blue);font-weight:700;font-size:8.4px;line-height:11px}
.p{position:absolute;left:10px;right:40px;color:var(--ink);font-weight:600;font-size:8.4px;line-height:10.8px}
.p b{color:var(--dark);font-weight:700}
.p.ind{padding-left:7px;text-indent:-7px}
.contact-title{position:absolute;left:0;width:397px;top:56px;text-align:center;color:var(--blue);font-weight:800;font-size:23px}
.block{position:absolute;left:20px;font-size:11.4px;line-height:13.4px;color:var(--dark);font-weight:600}
.block .name{color:var(--blue);font-weight:700}
.photo{position:absolute;left:259px;top:124px;width:119px;height:186px;background:linear-gradient(180deg,#a9b8c6 0%,#c9d6e2 40%,#b8c7d5 100%)}
.web{position:absolute;left:20px;top:320px;font-size:11.4px;font-weight:700;color:var(--dark);display:flex;align-items:center;gap:4px}
</style>
</head>
<body>

<!-- shared bars -->
<svg width="0" height="0" style="position:absolute">
  <defs>
    <g id="topbar">
      <polygon points="38,0 60,0 76,22 56,22" fill="var(--accent)"/>
      <polygon points="52,0 397,0 397,22 70,22" fill="var(--navy)"/>
    </g>
    <g id="footbar">
      <polygon points="0,0 270,0 295,24 0,24" fill="var(--navy)"/>
      <polygon points="266,0 276,0 297,24 287,24" fill="var(--accent)"/>
    </g>
  </defs>
</svg>

<!-- Slide 20 -->
<section class="slide" style="left:2px;top:0">
  <svg class="top-bar" viewBox="0 0 397 22"><use href="#topbar"/></svg>
  <h1 class="title">The Critical Questions To Ask<br>Of Any Prospective Non-Control<br>Investor</h1>
  <p class="q" style="top:137px">Question #1: How many years has the firm been investing Non-Control Capital?</p>
  <p class="p" style="top:154px">- <b>Best Answer:</b> 5+ years investing as a team within the current firm</p>
  <p class="p ind" style="top:176px">- Indicates comfort and experience evaluating and making NCC investments with each other and increases likelihood of close</p>
  <p class="q" style="top:242px">Question #2: How may fully-invested Non-Control Capital funds in the firm's history?</p>
  <p class="p" style="top:258px">- <b>Best Answer:</b> 2+ fully-invested funds</p>
  <p class="p ind" style="top:280px">- Indicates experience and ability to close deals with the current regime—those firms without it may only be testing the waters and not have a long-term commitment to NCC investing</p>
  <svg class="foot" viewBox="0 0 397 26"><use href="#footbar"/></svg>
  <div class="page-num">20</div>
  <div class="brand"><span class="dot"></span>PINEBROOK</div>
</section>

<!-- Slide 21 -->
<section class="slide" style="left:402px;top:0">
  <svg class="top-bar" viewBox="0 0 397 22"><use href="#topbar"/></svg>
  <h1 class="title">The Critical Questions To Ask<br>Of Any Prospective Non-Control<br>Investor</h1>
  <p class="q" style="top:137px">Question #3: What percentage of the firm's voting investment committee are full-time Non-Control Capital investors?</p>
  <p class="p" style="top:162px">- <b>Best Answer:</b> Super-majority</p>
  <p class="p ind" style="top:184px">- Indicates commitment, experience, and focus on NCC and overcomes dependency on buyout heritage, if any</p>
  <p class="q" style="top:265px">Question #4: What is the number of Non-Control Capital investments made with the current firm and team?</p>
  <p class="p" style="top:290px">- <b>Best Answer:</b> 20+</p>
  <p class="p ind" style="top:310px">- Indicates long-term experience and comfort with current team, investment committee, and NCC investment assessment</p>
  <svg class="foot" viewBox="0 0 397 26"><use href="#footbar"/></svg>
  <div class="page-num">21</div>
  <div class="brand"><span class="dot"></span>PINEBROOK</div>
</section>

<!-- Slide 22 -->
<section class="slide" style="left:805px;top:0">
  <svg class="top-bar" viewBox="0 0 397 22"><use href="#topbar"/></svg>
  <h1 class="title">The Critical Questions To Ask<br>Of Any Prospective Non-Control<br>Investor</h1>
  <p class="q" style="top:135px">Question #5: What percentage of portfolio investments made are "sponsorless" (those without a change-of-control investor)?:</p>
  <p class="p ind" style="top:166px;left:14px">- Best Answer: 80%+ of all investments closed in the last 5 years (assumes current transaction is also sponsorless)</p>
  <p class="p ind" style="top:199px;left:14px">- Indicates ability to add-value as a sole minority investor and not simply as a back-up to another sponsor</p>
  <p class="q" style="top:237px">Question #6: Can the investor show quantifiable proof of their ability to assist portfolio companies with growth and improvement (assumes more than 20 exited Non-Control investments)?:</p>
  <p class="p ind" style="top:277px;left:14px">- Best Answer: Yes (company owners should evaluate investors on actual historical revenue, EBITDA, and employee growth impact and the results should exceed what the current management has achieved on their own over the past 3 years)</p>
  <p class="p ind" style="top:332px;left:14px;right:30px">- Indicates true value-added ability to help owners grow their businesses. Those without proof of their impact, or who are unwilling to disclose it, should be excluded</p>
  <svg class="foot" viewBox="0 0 397 26"><use href="#footbar"/></svg>
  <div class="page-num">22</div>
  <div class="brand"><span class="dot"></span>PINEBROOK</div>
</section>

<!-- Slide 23: Contact -->
<section class="slide" style="left:2px;top:402px">
  <svg class="top-bar" viewBox="0 0 397 22"><use href="#topbar"/></svg>
  <h1 class="contact-title">Contact Us</h1>
  <div class="block" style="top:96px">
    <div class="name">Daniel R. Moreno</div>
    <div>Principal</div>
    <div>41 Hollis Ridge Road, Suite 210</div>
    <div>Brookfield, CT&nbsp; 06804</div>
    <div>Direct: (555) 014-2210</div>
    <div style="font-weight:700">dmoreno@pinebrookcapital.com</div>
  </div>
  <div class="block" style="top:189px">
    <div class="name">Boston Office</div>
    <div>72 Alder Park Drive, Suite 300</div>
    <div>Beverly, MA 01915</div>
    <div>(555) 014-2200</div>
  </div>
  <div class="block" style="top:255px">
    <div class="name">San Francisco Office</div>
    <div>Two Harbor Plaza, Suite 820</div>
    <div>San Francisco, CA 94105</div>
    <div>(555) 014-2300</div>
  </div>
  <div class="web">
    <svg width="10" height="10" viewBox="0 0 10 10" fill="none" stroke="#555" stroke-width=".8"><circle cx="5" cy="5" r="4.3"/><ellipse cx="5" cy="5" rx="1.8" ry="4.3"/><line x1=".7" y1="5" x2="9.3" y2="5"/></svg>
    www.pinebrookcapital.com
  </div>
  <div class="photo" role="img" aria-label="Portrait photo of the principal in a dark suit against a light blue-grey backdrop"></div>
  <svg class="foot" viewBox="0 0 397 26"><use href="#footbar"/></svg>
  <div class="page-num">23</div>
  <div class="brand"><span class="dot"></span>PINEBROOK</div>
</section>

<!-- Empty placeholders -->
<div class="slide empty" style="left:402px;top:402px"></div>
<div class="slide empty" style="left:805px;top:402px"></div>
<div class="slide empty" style="left:2px;top:805px"></div>
<div class="slide empty" style="left:402px;top:805px"></div>
<div class="slide empty" style="left:805px;top:805px"></div>

</body>
</html>
```